Create modern and sleek business card for luxury real estate company

We're a "boutique" real estate office looking for a design that gets across a highly modern luxury brand. Blacks and whites are probably the best colors unless we try a silver foil for the logo. I've attached a version of our current logo here. I'd like to swap out the current font on there with Gotham Light Regular.

I'm looking to have one side of the card have the logo with the space for our agents info on the other side.

Target Market(s)

Young professionals in a "luxury" headspace

Industry/Entity Type

Real estate

Contact Information for Business Card

A place for agent name, cell number, website. The slogan "Quietly Redefining Modern Living".

Font styles to use
Other font styles liked:
• Gotham Regular

Colors

Designer to choose only greyscale colors for use in the design.

Requirements
Must have
• Matte black as the background color. Clean lines and use of contrast. A specific design aspect that will use silver foil.
Nice to have
• Up in the air on integrating a QR code
Should not have
• Any houses or other real estate related design (ex: a clip art house)

```html
<!DOCTYPE html>
<html lang="en">
<head>
<meta charset="utf-8">
<title>Halden Realty Business Card</title>
<link href="https://fonts.googleapis.com/css2?family=Montserrat:wght@300;400;500&display=swap" rel="stylesheet">
<style>
  :root {
    --bg: #141414;
    --bg-edge: #080808;
    --card: #1c1c1c;
    --card-light: #262626;
    --silver: #d4d4d4;
    --silver-dim: #a9a9a9;
    --rule: #8c8c8c;
  }
  * { margin: 0; padding: 0; box-sizing: border-box; }
  html, body {
    width: 1200px; height: 900px; overflow: hidden;
    background: radial-gradient(ellipse at 50% 35%, var(--bg) 0%, var(--bg-edge) 100%);
    font-family: "Montserrat", sans-serif;
    color: var(--silver);
  }
  .stage { position: relative; width: 1200px; height: 900px; }
  .card {
    position: absolute;
    left: 285px;
    width: 630px; height: 360px;
    border-radius: 22px;
    background: linear-gradient(135deg, var(--card) 0%, var(--card-light) 60%, var(--card) 100%);
    box-shadow: 0 18px 40px rgba(0,0,0,0.7);
  }
  .card--front { top: 60px; }
  .card--back { top: 470px; }

  .brand { display: flex; align-items: center; gap: 20px; }
  .brand__mark {
    width: 78px; height: 78px; border-radius: 50%;
    border: 2px solid var(--silver);
    flex: none;
  }
  .brand__name {
    font-weight: 400; font-size: 40px; line-height: 1.12;
    letter-spacing: 2px; text-transform: uppercase; color: var(--silver);
  }
  .card--front .brand {
    position: absolute; left: 50%; top: 50%;
    transform: translate(-50%, -50%);
  }

  .card--back .brand { position: absolute; left: 48px; top: 110px; }
  .card--back .brand__mark { width: 64px; height: 64px; }
  .card--back .brand__name { font-size: 31px; }

  .divider {
    position: absolute; left: 360px; top: 84px;
    width: 1px; height: 150px; background: var(--rule);
  }
  .agent { position: absolute; left: 386px; top: 92px; }
  .agent__name { font-weight: 500; font-size: 20px; letter-spacing: 1.5px; text-transform: uppercase; }
  .agent__title { font-weight: 400; font-size: 14px; color: var(--silver-dim); margin-top: 2px; }
  .contact { list-style: none; margin-top: 20px; }
  .contact__item {
    display: flex; align-items: center; gap: 8px;
    font-size: 15px; font-weight: 400; letter-spacing: 0.5px; margin-bottom: 6px;
  }
  .contact__icon { width: 13px; height: 13px; flex: none; }
  .tagline {
    position: absolute; left: 0; right: 0; bottom: 38px;
    text-align: center; font-size: 15px; font-weight: 400;
    letter-spacing: 2px; text-transform: uppercase; color: var(--silver);
  }
</style>
</head>
<body>
<main class="stage">
  <section class="card card--front">
    <div class="brand">
      <span class="brand__mark"></span>
      <span class="brand__name">Halden<br>Realty</span>
    </div>
  </section>

  <section class="card card--back">
    <div class="brand">
      <span class="brand__mark"></span>
      <span class="brand__name">Halden<br>Realty</span>
    </div>
    <div class="divider"></div>
    <div class="agent">
      <p class="agent__name">Daniel Reyes</p>
      <p class="agent__title">Director</p>
      <ul class="contact">
        <li class="contact__item">
          <svg class="contact__icon" viewBox="0 0 24 24" fill="none" stroke="#d4d4d4" stroke-width="2"><path d="M5 3h4l2 5-2.5 1.5a11 11 0 0 0 6 6L16 13l5 2v4a2 2 0 0 1-2 2A16 16 0 0 1 3 5a2 2 0 0 1 2-2z"/></svg>
          555.014.2290
        </li>
        <li class="contact__item">
          <svg class="contact__icon" viewBox="0 0 24 24" fill="none" stroke="#d4d4d4" stroke-width="2"><rect x="3" y="5" width="18" height="14" rx="1"/><path d="M3 6l9 7 9-7"/></svg>
          hello@haldenrealty.com
        </li>
        <li class="contact__item">
          <svg class="contact__icon" viewBox="0 0 24 24" fill="none" stroke="#d4d4d4" stroke-width="2"><circle cx="12" cy="12" r="9"/><path d="M3 12h18M12 3c3 3 3 15 0 18M12 3c-3 3-3 15 0 18"/></svg>
          www.haldenrealty.com
        </li>
      </ul>
    </div>
    <p class="tagline">Quietly Redefining Modern Living</p>
  </section>
</main>
</body>
</html>
```